Electric mountain bike tours nz

We are an Electric Mountain bike tour company in New Zealand. We will be offering bike rental and guided tours around the Nelson region in New Zealand. I want our website to represent both Mountain biking and New Zealand with the colours layout and features. We want tabs for the following:
-1 about us
-2 what we offer
-3 bookings/contact
Under the about us tab will be who we are as a a company. I want the ability to add videos to each of these tabs as we move foward with videos of the tracks we will be riding. I want the website to be editable so I can add and remove videos/photos myself. Also "our bikes" will be under this tab.
Under the what we offer tab will be
-1 bike rental and pricing
-2 guided tours and pricing
-3 recommended package deals.
I want to able to put the tracks under the guided tours tab and select beginner/ intermediate/advanced and have the tracks in each of the following to match the rider level. Also to be able to have a small video of the track would be great in this section.
Bookings and contact tab
(Further information for this tab to be updated soon)
Coded - Design and coding required
1 page
- Silver ferns, kiwi, mountains

```html
<!DOCTYPE html>
<html lang="en">
<head>
<meta charset="utf-8">
<title>TRAILVOLT – Electric Mountain Bike Tours</title>
<link rel="stylesheet" href="https://fonts.googleapis.com/css2?family=Montserrat:wght@400;500;600;700;800&family=Open+Sans:ital,wght@0,400;0,600;0,700;1,400&display=swap">
<style>
:root{
  --orange:#f0712b;
  --ink:#1f1f1f;
  --text:#555;
  --muted:#8a8a8a;
  --grey-band:#a6a6a6;
  --pale:#f3f3f3;
  --line:#dcdcdc;
  --white:#fff;
  --forest:#23301c;
}
*{box-sizing:border-box;margin:0;padding:0}
html,body{width:1200px;height:3403px;overflow:hidden;background:var(--white)}
body{font-family:"Open Sans",Arial,sans-serif;color:var(--text);position:relative}
.page{position:relative;width:1200px;height:3403px;overflow:hidden}
.abs{position:absolute}
h1,h2,h3,.nav a,.btn{font-family:"Montserrat",Arial,sans-serif}

/* header */
.site-header{left:0;top:0;width:1200px;height:91px;background:var(--white);z-index:3}
.brand{left:96px;top:22px;display:flex;align-items:center;gap:12px}
.brand-dot{width:44px;height:44px;border-radius:50%;background:var(--ink)}
.brand-name{font-family:"Montserrat",sans-serif;font-weight:800;font-size:30px;color:var(--ink);letter-spacing:1px}
.nav{right:90px;top:38px;display:flex;gap:32px;align-items:center}
.nav a{font-size:15px;font-weight:600;color:var(--ink);text-decoration:none;text-transform:uppercase}
.nav a.active{color:var(--orange)}

/* hero */
.hero{left:0;top:91px;width:1200px;height:585px;background:linear-gradient(180deg,#3c5a7a 0%,#5b6f6c 30%,#6b6a3e 60%,#3b3a22 100%)}
.hero-title{left:0;top:210px;width:1200px;text-align:center;color:var(--white);font-weight:800;font-size:56px;line-height:70px;letter-spacing:1px;text-shadow:0 2px 6px rgba(0,0,0,.35)}
.btn{display:inline-block;text-transform:uppercase;font-weight:600;text-align:center}
.btn-solid{background:var(--orange);color:var(--white)}
.btn-outline{border:2px solid var(--orange);color:var(--orange);background:var(--white)}
.hero-cta{left:517px;top:379px;width:168px;height:56px;line-height:56px;font-size:18px}
.hero-dots{left:568px;top:607px;display:flex;gap:6px}
.hero-dots span{width:12px;height:12px;border-radius:50%;border:2px solid var(--white)}
.hero-dots span.on{background:var(--white)}

/* welcome */
.welcome{left:0;top:676px;width:1200px;height:585px;background:#f8f8f8}
.welcome-box{left:98px;top:88px;width:567px;height:404px;border:1px solid #9a9a9a;padding:36px 30px}
.section-title{font-weight:700;color:var(--ink);font-size:34px;letter-spacing:.5px}
.welcome-box p{font-size:13.5px;line-height:27px;margin-top:16px;width:460px}
.welcome-box .btn{margin-top:30px;width:124px;height:46px;line-height:42px;font-size:15px}
.welcome-video{left:619px;top:127px;width:483px;height:324px;background:linear-gradient(160deg,#2f3f25,#6a5a3a 60%,#b49a70)}
.play{left:214px;top:134px}

/* pricing */
.pricing{left:0;top:1261px;width:1200px;height:726px;background:var(--pale)}
.pricing .section-title{position:absolute;top:70px;width:1200px;text-align:center}
.plan{top:152px;width:322px;height:492px;background:var(--white);border:1px solid var(--line)}
.plan h3{height:59px;line-height:62px;text-align:center;font-weight:500;font-size:24px;color:var(--ink);letter-spacing:1px}
.plan-price{height:84px;background:var(--grey-band);color:var(--white);display:flex;align-items:center;justify-content:center;font-family:"Montserrat",sans-serif}
.plan.featured .plan-price{background:var(--orange)}
.plan.featured h3{background:var(--white)}
.amount{font-size:42px;font-weight:700}
.amount sup{font-size:22px;vertical-align:18px}
.per{font-size:18px;margin-left:6px;margin-top:14px}
.features{list-style:none;padding:34px 0 0 24px}
.features li{display:flex;align-items:center;font-size:14px;height:43px;color:#555}
.features li svg{margin-right:12px}
.features b{color:var(--ink);margin-left:6px}
.plan .btn{position:absolute;left:105px;top:407px;width:112px;height:46px;line-height:42px;font-size:15px}
.plan.featured .btn{border:none;line-height:46px}

/* rental */
.rental{left:0;top:1987px;width:1200px;height:530px;background:#f8f8f8}
.rental-photo{left:27px;top:88px;width:513px;height:295px;background:radial-gradient(ellipse at center,#3a3a3a 0%,#9a9a9a 55%,#f8f8f8 72%)}
.rental h2{left:594px;top:96px;font-size:34px;line-height:46px;font-weight:700;color:var(--ink);letter-spacing:.5px}
.rental p{left:594px;top:208px;width:500px;font-size:13.5px;line-height:28px}
.rental .btn{left:594px;top:379px;width:124px;height:46px;line-height:42px;font-size:15px}

/* testimonials */
.testimonials{left:0;top:2517px;width:1200px;height:495px;background:radial-gradient(ellipse at 30% 40%,#4a5a2c 0%,#2a3520 50%,#1a2015 100%)}
.testimonials h2{position:absolute;top:78px;width:1200px;text-align:center;color:var(--white);font-size:34px;font-weight:700}
.quote{top:200px;width:306px;height:197px;border:2px solid rgba(255,255,255,.85);text-align:center;color:var(--white);padding:62px 18px 0}
.quote p{font-style:italic;font-size:13.5px;line-height:24px}
.quote h4{font-family:"Open Sans",sans-serif;font-weight:600;font-size:18px;margin-top:14px}
.avatar{position:absolute;left:112px;top:-42px;width:82px;height:82px;border-radius:50%;border:3px solid var(--white);background:linear-gradient(135deg,#c9b4a0,#7d6a5c)}
.arrow{top:282px;width:40px;height:40px;border-radius:50%;background:rgba(255,255,255,.25);display:flex;align-items:center;justify-content:center}

/* footer */
.site-footer{left:0;top:3012px;width:1200px;height:391px;background:#f8f8f8}
.kiwi-art{left:86px;top:68px;width:250px;height:197px;background:radial-gradient(ellipse at 50% 45%,#8a5a34 0%,#7bb63f 55%,#f8f8f8 75%)}
.foot-col h3{font-family:"Montserrat",sans-serif;font-weight:500;font-size:20px;color:var(--ink)}
.quick{left:392px;top:88px}
.quick ul{list-style:none;margin-top:18px}
.quick li{font-size:12px;line-height:25px;color:#555}
.news{left:594px;top:88px;width:260px}
.news p{font-size:12px;line-height:22px;margin-top:20px}
.news .field{margin-top:16px;border-bottom:1px solid #bbb;font-size:12px;color:#999;padding:0 0 6px 16px}
.news .btn{margin-top:28px;width:92px;height:34px;line-height:34px;font-size:12px}
.contact{left:918px;top:88px}
.contact ul{list-style:none;margin-top:22px}
.contact li{display:flex;align-items:flex-start;font-size:12px;line-height:18px;margin-bottom:18px;color:#555}
.contact li svg{margin-right:16px;flex:none;margin-top:2px}
.foot-rule{left:98px;top:311px;width:1004px;height:1px;background:#e2e2e2}
.copyright{left:102px;top:332px;font-size:12px;color:#555}
.social{left:981px;top:326px;display:flex;gap:10px}
.social span{width:24px;height:24px;border-radius:50%;border:2px solid var(--orange)}
</style>
</head>
<body>
<div class="page">

  <header class="site-header abs">
    <div class="brand abs"><span class="brand-dot"></span><span class="brand-name">TRAILVOLT</span></div>
    <nav class="nav abs">
      <a class="active" href="#">Home</a>
      <a href="#">About Us</a>
      <a href="#">What We Offer</a>
      <a href="#">Bookings</a>
      <a href="#">Contact Us</a>
      <svg width="16" height="16" viewBox="0 0 16 16"><circle cx="6.5" cy="6.5" r="5" fill="none" stroke="#1f1f1f" stroke-width="2"/><line x1="10.5" y1="10.5" x2="15" y2="15" stroke="#1f1f1f" stroke-width="2.4"/></svg>
    </nav>
  </header>

  <section class="hero abs" role="img" aria-label="Electric mountain bike parked on a tussock hillside above a lake and mountains">
    <h1 class="hero-title abs">ELECTRIC MOUNTAIN BIKE<br>TOURS IN NEW ZEALAND</h1>
    <a class="btn btn-solid hero-cta abs">Book Now!</a>
    <div class="hero-dots abs"><span class="on"></span><span></span><span></span><span></span></div>
  </section>

  <section class="welcome abs">
    <div class="welcome-box abs">
      <h2 class="section-title">WELCOME TO TRAILVOLT</h2>
      <p>At vero eos et accusamus et iusto odio dignissimos ducimus qui blandit iis praesentium voluptatum deleniti atqu.</p>
      <p>Corrupti quos dolores et quas molestias excepturi sint occaecati cupidit ate non provident, similique sunt in culpa qui officia deserunt mollitian eni, id est laborum et dolorum fu m quidem rerum facilis est et expdita distincti am libero tempore, cum soluta no.</p>
      <a class="btn btn-outline">Read More</a>
    </div>
    <div class="welcome-video abs" role="img" aria-label="Video still of an e-bike beside a forest trail sign">
      <svg class="play abs" width="56" height="56" viewBox="0 0 56 56"><circle cx="28" cy="28" r="26" fill="none" stroke="#fff" stroke-width="3"/><path d="M22 17 L40 28 L22 39Z" fill="#fff"/></svg>
    </div>
  </section>

  <section class="pricing abs">
    <h2 class="section-title">OUR PRICING</h2>

    <div class="plan abs" style="left:98px">
      <h3>BASIC</h3>
      <div class="plan-price"><span class="amount">$99<sup>99</sup></span><span class="per">per month</span></div>
      <ul class="features">
        <li><svg width="14" height="12" viewBox="0 0 14 12"><path d="M1 6 L5 10 L13 1" fill="none" stroke="#f0712b" stroke-width="2.6"/></svg>At vero eos et accusamus et :<b>$56</b></li>
        <li><svg width="14" height="12" viewBox="0 0 14 12"><path d="M1 6 L5 10 L13 1" fill="none" stroke="#f0712b" stroke-width="2.6"/></svg>Blanditiis praesent :<b>$60</b></li>
        <li><svg width="14" height="12" viewBox="0 0 14 12"><path d="M1 6 L5 10 L13 1" fill="none" stroke="#f0712b" stroke-width="2.6"/></svg>Dignissimos duci qui :<b>$600 Monthly</b></li>
        <li><svg width="14" height="12" viewBox="0 0 14 12"><path d="M1 6 L5 10 L13 1" fill="none" stroke="#f0712b" stroke-width="2.6"/></svg>Sit voluptatem accusa :<b>$4</b></li>
        <li><svg width="14" height="12" viewBox="0 0 14 12"><path d="M1 6 L5 10 L13 1" fill="none" stroke="#f0712b" stroke-width="2.6"/></svg>Aliquam quaerat :<b>Every 24 hours</b></li>
      </ul>
      <a class="btn btn-outline">Sign Up</a>
    </div>

    <div class="plan featured abs" style="left:438px">
      <h3>STANDARD</h3>
      <div class="plan-price"><span class="amount">$199<sup>99</sup></span><span class="per">per month</span></div>
      <ul class="features">
        <li><svg width="14" height="12" viewBox="0 0 14 12"><path d="M1 6 L5 10 L13 1" fill="none" stroke="#f0712b" stroke-width="2.6"/></svg>At vero eos et accusamus et :<b>$56</b></li>
        <li><svg width="14" height="12" viewBox="0 0 14 12"><path d="M1 6 L5 10 L13 1" fill="none" stroke="#f0712b" stroke-width="2.6"/></svg>Blanditiis praesent :<b>$60</b></li>
        <li><svg width="14" height="12" viewBox="0 0 14 12"><path d="M1 6 L5 10 L13 1" fill="none" stroke="#f0712b" stroke-width="2.6"/></svg>Dignissimos duci qui :<b>$600 Monthly</b></li>
        <li><svg width="14" height="12" viewBox="0 0 14 12"><path d="M1 6 L5 10 L13 1" fill="none" stroke="#f0712b" stroke-width="2.6"/></svg>Sit voluptatem accusa :<b>$4</b></li>
        <li><svg width="14" height="12" viewBox="0 0 14 12"><path d="M1 6 L5 10 L13 1" fill="none" stroke="#f0712b" stroke-width="2.6"/></svg>Aliquam quaerat :<b>Every 24 hours</b></li>
      </ul>
      <a class="btn btn-solid">Sign Up</a>
    </div>

    <div class="plan abs" style="left:778px">
      <h3>PREMIUM</h3>
      <div class="plan-price"><span class="amount">$299<sup>99</sup></span><span class="per">per month</span></div>
      <ul class="features">
        <li><svg width="14" height="12" viewBox="0 0 14 12"><path d="M1 6 L5 10 L13 1" fill="none" stroke="#f0712b" stroke-width="2.6"/></svg>At vero eos et accusamus et :<b>$56</b></li>
        <li><svg width="14" height="12" viewBox="0 0 14 12"><path d="M1 6 L5 10 L13 1" fill="none" stroke="#f0712b" stroke-width="2.6"/></svg>Blanditiis praesent :<b>$60</b></li>
        <li><svg width="14" height="12" viewBox="0 0 14 12"><path d="M1 6 L5 10 L13 1" fill="none" stroke="#f0712b" stroke-width="2.6"/></svg>Dignissimos duci qui :<b>$600 Monthly</b></li>
        <li><svg width="14" height="12" viewBox="0 0 14 12"><path d="M1 6 L5 10 L13 1" fill="none" stroke="#f0712b" stroke-width="2.6"/></svg>Sit voluptatem accusa :<b>$4</b></li>
        <li><svg width="14" height="12" viewBox="0 0 14 12"><path d="M1 6 L5 10 L13 1" fill="none" stroke="#f0712b" stroke-width="2.6"/></svg>Aliquam quaerat :<b>Every 24 hours</b></li>
      </ul>
      <a class="btn btn-outline">Sign Up</a>
    </div>
  </section>

  <section class="rental abs">
    <div class="rental-photo abs" role="img" aria-label="Black electric mountain bike, side view"></div>
    <h2 class="abs">OFFERING BIKE RENTAL<br>AND GUIDED TOURS</h2>
    <p class="abs">Nam libero tempore, cum soluta nobis est eligendi optio cumque nihil impedit quo minus id quod maxime placeat facere possimus, omnis voluptas assumenda est, omnis dolor repellendus. Temporibus autem quibusdam et aut officiis de bitis aut rerum necessitatibus saepe eveniet ut et voluptates repudiandae sint et molestiae non recusanda um rerum hic tene.</p>
    <a class="btn btn-outline abs">Read More</a>
  </section>

  <section class="testimonials abs" role="img" aria-label="Close-up of green silver fern fronds">
    <h2>CLIENT TESTIMONIALS</h2>
    <div class="arrow abs" style="left:25px"><svg width="12" height="14" viewBox="0 0 12 14"><path d="M9 1 L3 7 L9 13" fill="none" stroke="#fff" stroke-width="2.4"/></svg></div>
    <div class="quote abs" style="left:100px">
      <span class="avatar" role="img" aria-label="Portrait of Rosa Penfold"></span>
      <p>Nam libero tempore, cum soluta nobis est eligendi optio cumque nihil impedit quo minus id quod maxime placea</p>
      <h4>Rosa Penfold</h4>
    </div>
    <div class="quote abs" style="left:447px">
      <span class="avatar" role="img" aria-label="Portrait of Grace Tolland"></span>
      <p>Nam libero tempore, cum soluta nobis est eligendi optio cumque nihil impedit quo minus id quod maxime placea</p>
      <h4>Grace Tolland</h4>
    </div>
    <div class="quote abs" style="left:794px">
      <span class="avatar" role="img" aria-label="Portrait of Owen Marsh"></span>
      <p>Nam libero tempore, cum soluta nobis est eligendi optio cumque nihil impedit quo minus id quod maxime placea</p>
      <h4>Owen Marsh</h4>
    </div>
    <div class="arrow abs" style="left:1132px"><svg width="12" height="14" viewBox="0 0 12 14"><path d="M3 1 L9 7 L3 13" fill="none" stroke="#fff" stroke-width="2.4"/></svg></div>
  </section>

  <footer class="site-footer abs">
    <div class="kiwi-art abs" role="img" aria-label="Cartoon kiwi bird riding a green bicycle"></div>

    <div class="foot-col quick abs">
      <h3>Quick Links</h3>
      <ul><li>Help</li><li>FAQ</li><li>Support</li><li>Sitemap</li><li>Terms Of Use</li><li>Privacy Statement</li></ul>
    </div>

    <div class="foot-col news abs">
      <h3>Newsletter Subscription</h3>
      <p>Register your Email Address to get Information about us</p>
      <div class="field">Email Address</div>
      <a class="btn btn-solid">Subscribe</a>
    </div>

    <div class="foot-col contact abs">
      <h3>Contact Us</h3>
      <ul>
        <li><svg width="12" height="16" viewBox="0 0 12 16"><path d="M6 0 C2.7 0 0 2.6 0 5.8 C0 10 6 16 6 16 C6 16 12 10 12 5.8 C12 2.6 9.3 0 6 0Z" fill="#f0712b"/><circle cx="6" cy="6" r="2.2" fill="#fff"/></svg><span>PO Box 482<br>Harbourview Central, 7020</span></li>
        <li><svg width="14" height="14" viewBox="0 0 14 14"><path d="M3 0 L5.5 3.5 L4 5.5 C5 7.5 6.5 9 8.5 10 L10.5 8.5 L14 11 L12 14 C6 14 0 8 0 2Z" fill="#f0712b"/></svg><span>1 555 204 3190</span></li>
        <li><svg width="14" height="14" viewBox="0 0 14 14"><rect x="3" y="0" width="8" height="5" fill="#f0712b"/><rect x="0" y="5" width="14" height="9" rx="1" fill="#f0712b"/><rect x="3" y="8" width="8" height="2" fill="#fff"/></svg><span>1 555 204 3191</span></li>
        <li><svg width="14" height="11" viewBox="0 0 14 11"><rect width="14" height="11" rx="1" fill="#f0712b"/><path d="M1 1 L7 6 L13 1" fill="none" stroke="#fff" stroke-width="1.4"/></svg><span>hello@trailvolt.co</span></li>
      </ul>
    </div>

    <div class="foot-rule abs"></div>
    <div class="copyright abs">Copyrights © 2018, TRAILVOLT. All rights reserved.</div>
    <div class="social abs"><span></span><span></span><span></span><span></span></div>
  </footer>

</div>
</body>
</html>
```